Tiller Row 100% real ingredients

I need a label design for my hummus.
"The Flint" Hummus
Roasted Red Pepper hummus infused with Crushed Red Pepper for a kick
Made With Real Ingredients
Oil Free
Preservative Free
in small print: TillerRowNaturalFoods.com
I also need an ingredient list
Chickpeas, Tahini, Red bell pepper, Sweet onion, Garlic, Water, Lemon, Maple syrup, Crushed red pepper, Pink Himalayan salt, Cumin, Cayenne, Black pepper,Baking soda
In our Hummus:
We believe that our hummus doesn't need all the extra ingredients like oils and preservatives. We want you to feel good after eating our products while also eating good food that is good for you! So we use fresh ingredients like lemon, garlic, red peppers, and sweet onions.
In the design can you put a red roasted pepper in the background?
Two of the pictures I uploaded are examples of what I would like it to look like.

```html
<!DOCTYPE html>
<html lang="en">
<head>
<meta charset="utf-8">
<title>The Flint Hummus – Label Set</title>
<link rel="stylesheet" href="https://fonts.googleapis.com/css2?family=Barlow:wght@400;500&family=Kaushan+Script&family=Playfair+Display:wght@700;900&display=swap">
<style>
  :root{
    --red:#a81419;
    --black:#0b0b0b;
    --ink:#111;
    --grey:#6f6f6f;
    --white:#fff;
    --board:#f1f1f1;
    --board-dark:#e2e2e2;
    --dim:#222;
  }
  *{box-sizing:border-box;margin:0;padding:0}
  html,body{width:1200px;height:815px;overflow:hidden;background:var(--white)}
  body{position:relative;font-family:"Barlow",Arial,sans-serif;color:var(--ink)}

  /* dimension marks */
  .dim{position:absolute;background:var(--dim)}
  .dim-h{height:1px}
  .dim-v{width:1px}
  .tick-v{position:absolute;width:1px;height:22px;background:var(--dim)}
  .tick-h{position:absolute;height:1px;width:22px;background:var(--dim)}
  .dim-label{position:absolute;font:500 16px/1 "Barlow",Arial,sans-serif;color:var(--dim);transform:translate(-50%,-50%);white-space:nowrap}

  /* labels */
  .label{position:absolute;overflow:hidden;background:linear-gradient(180deg,var(--board) 0%,#fafafa 40%,var(--board-dark) 100%)}
  .label-front{left:147px;top:172px;width:423px;height:176px;border-radius:11px}
  .label-back{left:147px;top:514px;width:423px;height:177px;border-radius:11px}
  .label-square{left:731px;top:213px;width:389px;height:389px;border-radius:12px}

  .photo{position:absolute;background:
      radial-gradient(circle at 62% 40%,#d8341d 0%,#b8200f 30%,rgba(184,32,15,0) 55%),
      radial-gradient(circle at 40% 30%,#fdfdfd 0%,#f1f1f1 60%,#e0e0e0 100%)}
  .label-front .photo,.label-back .photo{left:243px;top:0;width:180px;height:95px;border-bottom-left-radius:90px 95px}
  .label-square .photo{left:194px;top:0;width:195px;height:198px;border-bottom-left-radius:195px}

  .sidebar{position:absolute;left:0;top:0;width:92px;height:130px;background:var(--red)}
  .weight-box{position:absolute;left:0;top:130px;width:92px;height:46px;background:var(--black);color:var(--white);text-align:center;font-family:"Playfair Display",Georgia,serif;font-weight:700}
  .weight-box .wt-caption{display:block;font-size:10px;margin-top:6px;line-height:1}
  .weight-box .wt-value{display:block;font-size:18px;line-height:1.1;font-weight:900}

  .claim{position:absolute;text-align:center;color:var(--white);font:700 9.5px/1.15 "Playfair Display",Georgia,serif}
  .claim svg{display:block;margin:0 auto 2px}

  .brand-name{position:absolute;font-family:"Playfair Display",Georgia,serif;font-weight:700;color:var(--ink);white-space:nowrap;line-height:1}

  .tagline{position:absolute;font-family:"Kaushan Script",cursive;color:var(--red);white-space:nowrap;transform:rotate(-2deg)}
  .product-name{position:absolute;font:900 30px/1 "Playfair Display",Georgia,serif;color:var(--ink);white-space:nowrap}
  .descriptor{position:absolute;font:700 11.5px/1.2 "Playfair Display",Georgia,serif;color:var(--grey);letter-spacing:.2px;white-space:nowrap}

  /* back label */
  .section-head{position:absolute;left:18px;font:400 14px/1 "Kaushan Script",cursive;color:var(--red)}
  .body-copy{position:absolute;left:18px;font:400 8.6px/10.7px "Barlow",Arial,sans-serif;color:var(--ink);white-space:nowrap}
  .footer-band{position:absolute;left:0;bottom:0;width:100%;height:26px;background:var(--red);color:var(--white);text-align:center;font:700 12.5px/26px "Playfair Display",Georgia,serif;letter-spacing:.2px}

  /* square label band */
  .claim-band{position:absolute;left:0;top:309px;width:389px;height:80px;background:var(--red);color:var(--white)}
  .claim-band .claim{top:11px;font-size:10.5px}
  .band-weight{position:absolute;right:23px;top:22px;font:700 11.5px/1 "Playfair Display",Georgia,serif;text-align:right}
  .band-weight b{font-size:21px;font-weight:900}
  .band-url{position:absolute;right:23px;top:50px;font:700 11px/1 "Playfair Display",Georgia,serif}
</style>
</head>
<body>

<svg width="0" height="0" style="position:absolute" aria-hidden="true">
  <defs>
    <symbol id="icon-no-oil" viewBox="0 0 24 24">
      <circle cx="12" cy="12" r="10.8" fill="none" stroke="#fff" stroke-width="1.3"/>
      <path d="M12 5.2C12 5.2 7.6 10.6 7.6 13.6a4.4 4.4 0 0 0 8.8 0C16.4 10.6 12 5.2 12 5.2Z" fill="#fff"/>
      <line x1="4.4" y1="4.4" x2="19.6" y2="19.6" stroke="#fff" stroke-width="1.3"/>
    </symbol>
    <symbol id="icon-no-preservative" viewBox="0 0 24 24">
      <circle cx="12" cy="12" r="10.8" fill="none" stroke="#fff" stroke-width="1.3"/>
      <path d="M10.4 6.5v4.2L7 17.4h10l-3.4-6.7V6.5" fill="none" stroke="#fff" stroke-width="1.1"/>
      <path d="M8.6 14.3h6.8l1.6 3.1H7Z" fill="#fff"/>
      <line x1="9.6" y1="6.5" x2="14.4" y2="6.5" stroke="#fff" stroke-width="1.1"/>
      <circle cx="12" cy="4.3" r=".7" fill="#fff"/>
      <line x1="4.4" y1="4.4" x2="19.6" y2="19.6" stroke="#fff" stroke-width="1.3"/>
    </symbol>
  </defs>
</svg>

<!-- dimensions: front label -->
<div class="dim dim-h" style="left:147px;top:146px;width:423px"></div>
<div class="tick-v" style="left:147px;top:135px"></div>
<div class="tick-v" style="left:570px;top:135px"></div>
<div class="dim-label" style="left:362px;top:129px">3.6 in.</div>
<div class="dim dim-v" style="left:125px;top:172px;height:176px"></div>
<div class="tick-h" style="left:108px;top:172px"></div>
<div class="tick-h" style="left:108px;top:348px"></div>
<div class="dim-label" style="left:97px;top:257px">1.5 in.</div>

<!-- dimensions: back label -->
<div class="dim dim-h" style="left:147px;top:488px;width:423px"></div>
<div class="tick-v" style="left:147px;top:477px"></div>
<div class="tick-v" style="left:570px;top:477px"></div>
<div class="dim-label" style="left:362px;top:471px">3.6 in.</div>
<div class="dim dim-v" style="left:125px;top:514px;height:177px"></div>
<div class="tick-h" style="left:108px;top:514px"></div>
<div class="tick-h" style="left:108px;top:691px"></div>
<div class="dim-label" style="left:97px;top:599px">1.5 in.</div>

<!-- dimensions: square label -->
<div class="dim dim-h" style="left:731px;top:157px;width:389px"></div>
<div class="tick-v" style="left:731px;top:146px"></div>
<div class="tick-v" style="left:1120px;top:146px"></div>
<div class="dim-label" style="left:930px;top:141px">3.3 in.</div>
<div class="dim dim-v" style="left:698px;top:213px;height:389px"></div>
<div class="tick-h" style="left:687px;top:213px"></div>
<div class="tick-h" style="left:687px;top:602px"></div>
<div class="dim-label" style="left:670px;top:385px">3.3 in.</div>

<!-- front label -->
<section class="label label-front">
  <div class="photo" role="img" aria-label="Roasted red peppers in a white bowl on a white wooden board"></div>
  <div class="sidebar">
    <div class="claim" style="left:0;width:92px;top:10px">
      <svg width="36" height="36"><use href="#icon-no-oil"/></svg>Oil free
    </div>
    <div class="claim" style="left:0;width:92px;top:63px">
      <svg width="36" height="36"><use href="#icon-no-preservative"/></svg>Preservative<br>free
    </div>
  </div>
  <div class="weight-box"><span class="wt-caption">Net Wt.:</span><span class="wt-value">340oz</span></div>

  <div class="brand-name" style="left:122px;top:48px;font-size:18px">Tiller Row</div>

  <div class="tagline" style="left:243px;top:86px;font-size:15px">Made with real ingredients</div>
  <div class="product-name" style="left:118px;top:108px">The Flint Hummus</div>
  <div class="descriptor" style="left:118px;top:142px">Roasted Red Pepper hummus infused with<br>Crushed Red Pepper for a kick</div>
</section>

<!-- back label -->
<section class="label label-back">
  <div class="photo" role="img" aria-label="Roasted red peppers in a white bowl on a white wooden board"></div>
  <h2 class="section-head" style="top:10px">In our Hummus:</h2>
  <p class="body-copy" style="top:25px">We believe that our hummus doesn't need all the<br>extra ingredients like oils and preservatives. We<br>want you to feel good after eating our products while<br>also eating good food that is good for you!<br>So we use fresh ingredients like lemon, garlic, red<br>peppers, and sweet onions.</p>
  <h2 class="section-head" style="top:97px">Ingredients:</h2>
  <p class="body-copy" style="top:113px">Organic Chickpeas, Organic Tahini, Organic Red Pepper, Sweet Onion, Garlic, Water, Lemon,<br>Maple Syrup, Crushed Red Pepper, Pink Himalayan Salt, Cumin, Cayenne, Black Pepper,<br>Baking Soda.</p>
  <div class="footer-band">TillerRowNaturalFoods.com</div>
</section>

<!-- square label -->
<section class="label label-square">
  <div class="photo" role="img" aria-label="Roasted red peppers in a white bowl on a white wooden board"></div>

  <div class="brand-name" style="left:40px;top:90px;font-size:30px">Tiller Row</div>

  <div class="tagline" style="left:160px;top:180px;font-size:21px">Made with real ingredients</div>
  <div class="product-name" style="left:37px;top:223px;font-size:36px">The Flint Hummus</div>
  <div class="descriptor" style="left:40px;top:264px;font-size:14.2px;line-height:16px">Roasted Red Pepper hummus infused with<br>Crushed Red Pepper for a kick</div>

  <div class="claim-band">
    <div class="claim" style="left:17px;width:80px">
      <svg width="39" height="39"><use href="#icon-no-oil"/></svg>Oil free
    </div>
    <div class="claim" style="left:87px;width:100px">
      <svg width="39" height="39"><use href="#icon-no-preservative"/></svg>Preservative free
    </div>
    <div class="band-weight">Net Wt.: <b>340oz</b></div>
    <div class="band-url">TillerRowNaturalFoods.com</div>
  </div>
</section>

</body>
</html>
```